Automotive eCommerce Business looking for a business card design

Looking for a clean and simple business card design. Our company name is "Brindle Auto" and we are a company specializing in the ecommerce sales of automotive parts, specifically for pick up trucks and large SUVs. Our company colours are red, black, and white.

Feel free to use the logo provided or create a new logo that you seem fit. Looking forward to your creative ideas!

Industry/Entity Type

Automotive

Contact Information for Business Card

We were thinking of a possibly two-sided design featuring just the logo and company name on one side, and personal information on the other side. Single sided designs will be considered as well.

Font styles to use
Serif
Sans Serif
Decorative

Colors
ec1f27
ffffff
000000

Requirements
Must have
• Space for employee's name, title, phone number and email address, along with the company address and website somewhere.

```html
<!DOCTYPE html>
<html lang="en">
<head>
<meta charset="utf-8">
<title>Brindle Auto Ltd. – Business Card</title>
<link rel="stylesheet" href="https://fonts.googleapis.com/css2?family=Roboto:wght@400;500;700&family=Roboto+Condensed:wght@500;700&display=swap">
<style>
  :root {
    --stage: #2a2a2a;
    --card-white: #f4f4f4;
    --brand-red: #9b1d20;
    --ink: #4a4a4a;
    --ink-soft: #555555;
    --band-grey: #4b4d4d;
    --rule: #c9c9c9;
    --paper: #ffffff;
  }
  * { margin: 0; padding: 0; box-sizing: border-box; }
  html, body { width: 1200px; height: 960px; overflow: hidden; }
  body {
    background: var(--stage);
    font-family: "Roboto", Arial, sans-serif;
    position: relative;
  }
  .card { position: absolute; width: 600px; height: 342px; }

  /* Front */
  .card-front { left: 314px; top: 113px; background: var(--card-white); }
  .brand-block {
    position: absolute; left: 40px; top: 88px; width: 270px;
    display: flex; flex-direction: column; align-items: center;
  }
  .brand-square { width: 108px; height: 108px; background: var(--brand-red); }
  .brand-name {
    margin-top: 26px;
    font-family: "Roboto", Arial, sans-serif;
    font-weight: 500; font-size: 21px; letter-spacing: 1px;
    text-transform: uppercase; color: var(--ink); white-space: nowrap;
  }
  .divider {
    position: absolute; left: 311px; top: 68px; width: 1px; height: 222px;
    background: var(--rule);
  }
  .contact { position: absolute; left: 335px; top: 72px; color: var(--ink-soft); }
  .person-name {
    font-family: "Roboto Condensed", Arial, sans-serif;
    font-weight: 700; font-size: 21px; color: var(--brand-red); line-height: 24px;
  }
  .person-title {
    font-family: "Roboto Condensed", Arial, sans-serif;
    font-weight: 500; font-size: 15px; color: var(--ink); line-height: 20px;
  }
  .address { margin-top: 12px; font-size: 14px; line-height: 19px; }
  .contact-list { margin-top: 12px; list-style: none; font-size: 14px; line-height: 19px; }
  .contact-list li { display: flex; align-items: center; gap: 8px; }
  .contact-list svg { width: 13px; height: 13px; fill: var(--brand-red); flex: none; }
  .card-band { position: absolute; left: 0; bottom: 0; width: 600px; height: 12px; }

  /* Back */
  .card-back {
    left: 311px; top: 472px; background: var(--brand-red);
    display: flex; flex-direction: column; align-items: center;
  }
  .back-square { margin-top: 86px; width: 112px; height: 112px; background: var(--paper); }
  .back-name {
    margin-top: 28px; font-weight: 500; font-size: 24px; letter-spacing: 1.5px;
    text-transform: uppercase; color: var(--paper);
  }
  .back-web {
    position: absolute; top: 298px; width: 100%; text-align: center;
    font-size: 14px; letter-spacing: 4.5px; color: var(--paper);
  }
</style>
</head>
<body>

<section class="card card-front" aria-label="Business card front">
  <div class="brand-block">
    <div class="brand-square"></div>
    <div class="brand-name">Brindle Auto Ltd.</div>
  </div>
  <div class="divider"></div>
  <div class="contact">
    <div class="person-name">MARCUS HALE</div>
    <div class="person-title">CEO/FOUNDER</div>
    <p class="address">4120 Alder Ridge Road<br>Fairbanks, Alaska 99712</p>
    <ul class="contact-list">
      <li><svg viewBox="0 0 16 16" aria-hidden="true"><path d="M3.6 1l2.6 2.9-1.4 2a9 9 0 0 0 5.3 5.3l2-1.4L15 12.4 13.4 15C6.8 15 1 9.2 1 2.6z"/></svg>907 555 0142</li>
      <li><svg viewBox="0 0 16 16" aria-hidden="true"><path d="M4 0h8v16H4zM5.5 1.5v11h5v-11zM7 13.5h2v1H7z" fill-rule="evenodd"/></svg>907 555 0187</li>
      <li><svg viewBox="0 0 16 16" aria-hidden="true"><path d="M4 1h8v4H4zM1 6h14v7h-3v2H4v-2H1zM5 10v4h6v-4z" fill-rule="evenodd"/></svg>907 555 0163</li>
      <li><svg viewBox="0 0 16 16" aria-hidden="true"><path d="M1 3h14v10H1zM2.5 4.5L8 8.5l5.5-4z" fill-rule="evenodd"/></svg>mail@brindleauto.com</li>
      <li><svg viewBox="0 0 16 16" aria-hidden="true"><circle cx="8" cy="8" r="7"/></svg>www.brindleauto.com</li>
    </ul>
  </div>
  <svg class="card-band" viewBox="0 0 600 12" aria-hidden="true">
    <polygon points="0,0 393,0 389,12 0,12" fill="var(--brand-red)"/>
    <polygon points="397,0 600,0 600,12 393,12" fill="var(--band-grey)"/>
  </svg>
</section>

<section class="card card-back" aria-label="Business card back">
  <div class="back-square"></div>
  <div class="back-name">Brindle Auto Ltd.</div>
  <div class="back-web">www.brindleauto.com</div>
</section>

</body>
</html>
```